​Silver Harbor Rhythm provides personal, friendly service in a fun and high energy environment. We are based in Vermont.

We would like a card that appeals to a wide range of audiences as we do a wide range of events. Please feel free to check out our website silverharborrhythm.net for inspiration.

Target Market(s)

weddings, corporate, birthday parties, colleges

Industry/Entity Type

Business

Contact Information for Business Card

Silver Harbor Rhythm
Providing Entertainment For All Occasions
555 274 9160
silverharborrhythm@mailnest.net
silverharborrhythm.net

```html
<!DOCTYPE html>
<html lang="en">
<head>
<meta charset="utf-8">
<title>Silver Harbor Rhythm – Business Card</title>
<link rel="stylesheet" href="https://fonts.googleapis.com/css2?family=Open+Sans:wght@400;600;700&display=swap">
<style>
  :root {
    --canvas-bg: #e9e6e2;
    --card-white: #ffffff;
    --maroon: #4a0f1a;
    --maroon-deep: #3a0a13;
    --forest: #2f6a24;
    --forest-dark: #265a1c;
    --text-light: #ffffff;
    --text-green: #2f6a24;
  }
  * { box-sizing: border-box; margin: 0; padding: 0; }
  html, body {
    width: 1200px; height: 1200px; overflow: hidden;
    background: var(--canvas-bg);
    font-family: "Open Sans", Arial, sans-serif;
  }
  .canvas { position: relative; width: 1200px; height: 1200px; }

  .card {
    position: absolute; left: 150px; width: 900px; height: 515px;
    border-radius: 24px; overflow: hidden;
    box-shadow: 0 6px 18px rgba(0,0,0,0.18);
  }
  .card-front { top: 70px; background: var(--card-white); }
  .card-back { top: 615px; background: var(--forest); }

  .front-shapes { position: absolute; inset: 0; width: 100%; height: 100%; }

  .brand {
    position: absolute; left: 58px; top: 120px;
    display: flex; align-items: center; gap: 14px;
  }
  .brand-mark { width: 22px; height: 22px; background: var(--text-green); }
  .brand-name {
    font-weight: 700; font-size: 40px; letter-spacing: 0.5px;
    color: var(--text-green);
  }

  .holder {
    position: absolute; left: 58px; top: 288px;
    font-size: 22px; color: var(--text-green);
  }
  .holder-name { font-weight: 700; }
  .holder-title { font-weight: 400; color: #333; }

  .contact {
    position: absolute; right: 40px; top: 275px;
    list-style: none; text-align: right; color: var(--text-light);
    font-size: 17px; line-height: 1;
  }
  .contact li { display: flex; justify-content: flex-end; align-items: center; gap: 8px; margin-bottom: 14px; }
  .contact .icon { width: 16px; height: 16px; flex: none; }
  .contact .address { margin-top: 30px; }

  .back-brand {
    position: absolute; left: 0; right: 0; top: 170px;
    display: flex; justify-content: center; align-items: center; gap: 18px;
  }
  .back-brand .brand-mark { width: 34px; height: 34px; background: var(--text-light); }
  .back-brand .brand-name { color: var(--text-light); font-size: 58px; }

  .back-url {
    position: absolute; left: 0; right: 0; top: 410px; text-align: center;
    font-weight: 600; font-size: 25px; letter-spacing: 2px; color: var(--text-light);
  }
</style>
</head>
<body>
<main class="canvas">

  <section class="card card-front" aria-label="Card front">
    <svg class="front-shapes" viewBox="0 0 900 515" preserveAspectRatio="none" aria-hidden="true">
      <path d="M690 0 L900 0 L900 515 L0 515 L0 450 C260 450 600 320 690 0 Z" fill="var(--maroon)"/>
      <path d="M0 398 C250 420 470 350 575 262 C490 380 260 452 0 446 Z" fill="var(--forest)"/>
    </svg>

    <div class="brand">
      <span class="brand-mark"></span>
      <span class="brand-name">Silver Harbor Rhythm</span>
    </div>

    <p class="holder"><span class="holder-name">Your Name,</span> <span class="holder-title">Title</span></p>

    <ul class="contact">
      <li>
        <svg class="icon" viewBox="0 0 16 16" aria-hidden="true"><circle cx="8" cy="8" r="8" fill="#fff"/><path d="M5 4 L7 4 L7.5 6.5 L6.5 7.3 C7 8.5 7.8 9.3 8.8 9.6 L9.6 8.6 L12 9.2 L12 11 C8 11.5 4.5 8 5 4 Z" fill="var(--maroon)"/></svg>
        <span>555 274 9160</span>
      </li>
      <li>
        <svg class="icon" viewBox="0 0 16 16" aria-hidden="true"><circle cx="8" cy="8" r="7" fill="none" stroke="#fff" stroke-width="1.6"/><path d="M1 8 H15 M8 1 C4 5 4 11 8 15 C12 11 12 5 8 1" fill="none" stroke="#fff" stroke-width="1.2"/></svg>
        <span>www.silverharborrhythm.net</span>
      </li>
      <li>
        <svg class="icon" viewBox="0 0 16 16" aria-hidden="true"><rect x="1" y="3" width="14" height="10" rx="1" fill="#fff"/><path d="M1.5 3.5 L8 9 L14.5 3.5" fill="none" stroke="var(--maroon)" stroke-width="1.3"/></svg>
        <span>silverharborrhythm@mailnest.net</span>
      </li>
      <li class="address"><span>Street Name, City Name, Zip Code-00000</span></li>
    </ul>
  </section>

  <section class="card card-back" aria-label="Card back">
    <div class="back-brand">
      <span class="brand-mark"></span>
      <span class="brand-name">Silver Harbor Rhythm</span>
    </div>
    <p class="back-url">www.silverharborrhythm.net</p>
  </section>

</main>
</body>
</html>
```